Redesign website bus travel company Falk Brenz

We require a complete redesign of the website of Reisebüro Falk Brenz, an established bus tour operator based in Graubünden (www.falkbrenz.ch). For years, the company has specialized in multi-day tours throughout Europe, as well as day trips such as shopping trips to Innsbruck or Como, music tours, and market visits, primarily for seniors, as well as car rentals for clubs and companies.

The new website requires a video header with overlay text, red as the primary corporate color, complemented by black and gray, and a highly simplified navigation with two main sections: "Our Trips" and "Bus Rental." The remaining sections must be accessible via the "Menu" menu item. The design should be user-friendly for all age groups and mobile-responsive.

The goal is a trustworthy, modern website that reflects personal service and many years of experience.
The new logo can be found in the files, as well as a few pictures.

Target Market(s)

Guests of bus tours (day and multi-day trips) and bus rentals (clubs, companies, etc.)

Industry/Entity Type

Busreisen und Busvermietung

Number of Pages Required

1 page

Requirements
Must have
• Red as primary color, video header, simple UX for target group seniors
Nice to have
• Photo galleries of destinations and the vehicle fleet

```html
<!DOCTYPE html>
<html lang="en">
<head>
<meta charset="utf-8">
<title>Falk Brenz – Bus Travel</title>
<link href="https://fonts.googleapis.com/css2?family=Open+Sans:wght@600;700&family=Figtree:wght@400;500;600;700&display=swap" rel="stylesheet">
<style>
:root{
  --red:#c8161d;
  --red-dark:#b01218;
  --ink:#1c1c1c;
  --text:#444;
  --muted:#777;
  --nav:#555;
  --footer:#4b4b4b;
  --light:#f2f2f2;
  --white:#fff;
  --dark-btn:#333;
}
*{box-sizing:border-box;margin:0;padding:0}
html,body{width:1200px;height:3526px;overflow:hidden}
body{font-family:"Figtree",sans-serif;color:var(--text);background:var(--white);position:relative}
.abs{position:absolute}
h2.section-title{font-family:"Open Sans",sans-serif;font-weight:700;color:var(--ink);font-size:32px;text-align:center;letter-spacing:.3px;position:relative}
.underline{position:relative;display:inline-block}
.underline::after{content:"";position:absolute;left:0;right:0;bottom:2px;height:3px;background:var(--red);opacity:.8}
.btn{display:inline-flex;align-items:center;justify-content:center;font-family:"Figtree",sans-serif;font-weight:700;font-size:14px;text-transform:uppercase;color:var(--white);background:var(--red);border-radius:4px;text-decoration:none}
.btn.dark{background:var(--dark-btn)}

/* header */
.topbar{top:0;left:0;width:1200px;height:70px;background:var(--white)}
.brand{font-family:"Figtree",sans-serif;font-weight:700;font-size:30px;color:var(--red);display:flex;align-items:center;gap:8px}
.brand .dot{width:14px;height:14px;background:var(--red);border-radius:50%}
.contact-item{display:flex;align-items:center;gap:10px}
.contact-item .icon{width:36px;height:36px;border-radius:50%;background:#2b2b2b;display:flex;align-items:center;justify-content:center}
.contact-item small{display:block;font-size:10px;color:var(--muted)}
.contact-item span{display:block;font-size:16px;color:var(--red)}
.mainnav{top:70px;left:0;width:1200px;height:40px;background:var(--nav);display:flex;align-items:center;padding-left:103px}
.mainnav a{color:var(--white);font-size:14px;text-decoration:none;height:40px;line-height:40px;padding:0 11px;margin-right:6px}
.mainnav a.active{background:var(--red)}

/* hero */
.hero{top:110px;left:0;width:1200px;height:570px;background:linear-gradient(180deg,#7d8a95 0%,#8e9a8c 40%,#5f7a3c 75%,#4b6a2a 100%)}
.hero-title{top:54px;width:1200px;text-align:center;font-family:"Open Sans",sans-serif;font-weight:700;font-size:46px;color:var(--white)}
.hero-sub{top:124px;left:180px;width:840px;text-align:center;font-size:15px;line-height:26px;color:var(--white)}
.play{top:458px;left:580px;width:40px;height:40px;border-radius:50%;background:var(--white);display:flex;align-items:center;justify-content:center}
.watch{top:528px;width:1200px;text-align:center;color:var(--white);font-size:14px;font-weight:500}

/* services */
.card{position:absolute;width:215px;height:199px;background:var(--white);box-shadow:0 2px 10px rgba(0,0,0,.08)}
.card .ph{height:155px}
.card p{height:44px;line-height:44px;text-align:center;font-size:15px;color:var(--ink)}

/* download band */
.band{top:1406px;left:0;width:1200px;height:299px;background:linear-gradient(180deg,#c8161d,#b5141a);text-align:center;color:var(--white)}
.band h2{font-family:"Open Sans",sans-serif;font-weight:700;font-size:32px;margin-top:52px}
.band .lead{font-size:16px;margin-top:20px}
.band .file{font-size:10px;margin-top:16px}
.dl{margin:18px auto 0;width:172px;height:43px;background:var(--white);color:var(--red);border-radius:4px;display:flex;align-items:center;justify-content:center;gap:10px;font-weight:700;font-size:14px}

/* trips + rental */
.block-title{font-family:"Open Sans",sans-serif;font-weight:700;font-size:32px;color:var(--ink)}
.trip{font-size:15px;line-height:27px;color:var(--ink)}
.trip b{color:var(--red);font-weight:400}
.price{font-size:12.5px;color:var(--red);margin-top:8px}
.dep{font-size:9.5px;color:var(--muted);margin-top:8px}
.checks li{list-style:none;font-size:13px;color:var(--muted);display:flex;align-items:center;gap:10px;margin-bottom:9px}

/* gallery */
.gallery{top:2716px;left:0;width:1200px;height:531px;background:var(--light)}
.gph{position:absolute}
.arrow{position:absolute;width:45px;height:44px;border-radius:4px;display:flex;align-items:center;justify-content:center}

/* footer */
.footer{top:3247px;left:0;width:1200px;height:279px;background:var(--footer);color:var(--white);text-align:center}
.footer .brand{color:var(--white);justify-content:center}
.footer nav a{color:var(--white);font-size:14px;text-decoration:none;margin:0 8px}
.social{width:28px;height:28px;border-radius:50%;background:var(--white);display:inline-flex;align-items:center;justify-content:center;margin:0 5px}
</style>
</head>
<body>

<header class="topbar abs">
  <div class="brand abs" style="left:103px;top:17px"><span>Falk Brenz</span></div>
  <div class="contact-item abs" style="left:522px;top:17px">
    <div class="icon"><svg width="18" height="14" viewBox="0 0 18 14"><rect x="1" y="1" width="16" height="12" rx="1" fill="none" stroke="#fff" stroke-width="1.6"/><path d="M1 2l8 6 8-6" fill="none" stroke="#fff" stroke-width="1.6"/></svg></div>
    <div><small>Email Address</small><span>info@falkbrenz.ch</span></div>
  </div>
  <div class="contact-item abs" style="left:733px;top:17px">
    <div class="icon"><svg width="16" height="16" viewBox="0 0 24 24"><path d="M6.6 10.8c1.4 2.8 3.8 5.1 6.6 6.6l2.2-2.2c.3-.3.7-.4 1-.2 1.1.4 2.3.6 3.6.6.6 0 1 .4 1 1V20c0 .6-.4 1-1 1C10.6 21 3 13.4 3 4c0-.6.4-1 1-1h3.5c.6 0 1 .4 1 1 0 1.3.2 2.5.6 3.6.1.3 0 .7-.2 1z" fill="#fff"/></svg></div>
    <div><small>Call Us now</small><span>+41(0)81 555 01 23</span></div>
  </div>
  <a class="btn abs" style="left:962px;top:16px;width:134px;height:40px">Contact</a>
</header>

<nav class="mainnav abs">
  <a class="active">Start</a><a>About Us</a><a>Day Trips</a><a>Holiday Trips</a><a>Group Tours</a><a>Airport Transfer</a><a>Minibus Rental</a><a>The Driver Making</a><a>Terms &amp; Conditions</a>
</nav>

<section class="hero abs" role="img" aria-label="Video header: couple in traditional costume with accordion and alphorn beside a tour coach in an alpine meadow">
  <h1 class="hero-title abs">THE 2025 TRAVEL PROGRAM IS HERE!</h1>
  <p class="hero-sub abs">You Can Find All Tours and Day Trips Online Under The Day Trips And Holiday Trips Sections Browse Through Them, There's Something For Everyone.</p>
  <a class="btn abs" style="left:516px;top:206px;width:168px;height:46px;font-size:15px">Get Started</a>
  <div class="play abs"><svg width="14" height="16" viewBox="0 0 14 16"><path d="M2 1l11 7-11 7z" fill="#333"/></svg></div>
  <div class="watch abs">WATCH VIDEO</div>
</section>

<section class="abs" style="top:680px;left:0;width:1200px;height:726px">
  <h2 class="section-title" style="margin-top:72px">WE ARE HAPPY <span class="underline">TO RECOMMEND</span> OURSELVES FOR</h2>
  <div class="card" style="left:144px;top:156px"><div class="ph" role="img" aria-label="Couple reading a map in a car" style="background:linear-gradient(135deg,#8a7a66,#c9b59a)"></div><p>Car Travel</p></div>
  <div class="card" style="left:376px;top:156px"><div class="ph" role="img" aria-label="Smiling hiker on a day trip" style="background:linear-gradient(135deg,#6d9cc8,#3e5f8a)"></div><p>Day Trips</p></div>
  <div class="card" style="left:609px;top:156px"><div class="ph" role="img" aria-label="Colourful carnival music parade" style="background:linear-gradient(135deg,#d0663a,#6a8fb0)"></div><p>Music Tours</p></div>
  <div class="card" style="left:841px;top:156px"><div class="ph" role="img" aria-label="Group of seniors on holiday" style="background:linear-gradient(135deg,#9c8e7c,#5d5448)"></div><p>Holiday Trips</p></div>
  <div class="card" style="left:144px;top:379px"><div class="ph" role="img" aria-label="Club members on an outing" style="background:linear-gradient(135deg,#b8443c,#8d9a88)"></div><p>Club Trips</p></div>
  <div class="card" style="left:376px;top:379px"><div class="ph" role="img" aria-label="Seniors laughing at a corporate party" style="background:linear-gradient(135deg,#a8b37a,#c99a7d)"></div><p>Corporate Events</p></div>
  <div class="card" style="left:609px;top:379px"><div class="ph" role="img" aria-label="Wedding couple outdoors" style="background:linear-gradient(135deg,#6f7d55,#3b3a33)"></div><p>Wedding Trips</p></div>
  <div class="card" style="left:841px;top:379px"><div class="ph" role="img" aria-label="Guests mingling at an event" style="background:linear-gradient(135deg,#4a4440,#a08c78)"></div><p>Events</p></div>
  <a class="btn abs" style="left:528px;top:619px;width:144px;height:43px">Get A Quote</a>
</section>

<section class="band abs">
  <h2><span class="underline">TRAVEL PROGRAM 2025</span> AS DOWNLOAD</h2>
  <p class="lead">Our Travel Industry Expertise, Friendly &amp; Reliable Service, and Competitive Prices Set Us Apart From The Competition.</p>
  <p class="file">JP 2025.pdf PageView document 9.3 MB</p>
  <div class="dl"><svg width="16" height="19" viewBox="0 0 16 19"><path d="M1 1h9l5 5v12H1z" fill="none" stroke="#c8161d" stroke-width="1.5"/><path d="M10 1v5h5" fill="none" stroke="#c8161d" stroke-width="1.5"/></svg>DOWNLOAD</div>
</section>

<div class="abs" role="img" aria-label="Two smiling men in front of the tour coach" style="left:144px;top:1767px;width:455px;height:443px;background:linear-gradient(135deg,#4f88b8,#5a5f66 60%,#2c2c2e)"></div>
<section class="abs" style="left:658px;top:1796px;width:394px">
  <h2 class="block-title"><span class="underline">OUR</span> TRIPS</h2>
  <p class="trip" style="margin-top:20px"><b>01.</b> Friday, 13.06.25 - Bannalpsee: Natural jewel &amp; insider tip in the canton of Nidwalden</p>
  <p class="price">CHF 102.-, including cable car and Alpine macaroni à discretion</p>
  <p class="dep">Departure from Chur Bahnhofplatz (in front of Hotel ABC) at 7.00 a.m.</p>
  <p class="trip" style="margin-top:14px;text-align:justify"><b>01.</b>Wednesday, 23.07.25 - Visiting the funny cider farmer in Bad Waldsee €</p>
  <p class="price">Fr. 92.-, including Mostzügle ride, coffee stop, snack &amp; schnapps</p>
  <p class="dep">Departure from Chur Bahnhofplatz (in front of Hotel ABC) at 7.30 a.m.</p>
</section>
<a class="btn abs" style="left:662px;top:2126px;width:143px;height:44px">Book A Trip</a>
<a class="btn dark abs" style="left:816px;top:2126px;width:144px;height:44px">Learn More</a>

<section class="abs" style="left:144px;top:2255px;width:420px">
  <h2 class="block-title"><span class="underline">BUS</span> RENTAL</h2>
  <p style="font-size:17px;color:var(--ink);margin-top:22px">Price</p>
  <p style="font-size:12.5px;color:var(--muted);line-height:24px;margin-top:6px">CHF 200.00, basic flat rate per day including 200 kmFr. 0.85 per additional kilometer</p>
  <p style="font-size:17px;color:var(--ink);margin-top:14px;margin-bottom:10px">Extra Costs</p>
  <ul class="checks">
    <li><svg width="13" height="13" viewBox="0 0 13 13"><circle cx="6.5" cy="6.5" r="6.5" fill="#c8161d"/><path d="M3.5 6.8l2 2 4-4" fill="none" stroke="#fff" stroke-width="1.6"/></svg>CHF 35.00, final interior cleaning</li>
    <li><svg width="13" height="13" viewBox="0 0 13 13"><circle cx="6.5" cy="6.5" r="6.5" fill="#c8161d"/><path d="M3.5 6.8l2 2 4-4" fill="none" stroke="#fff" stroke-width="1.6"/></svg>CHF 50.00, final interior and exterior cleaning</li>
    <li><svg width="13" height="13" viewBox="0 0 13 13"><circle cx="6.5" cy="6.5" r="6.5" fill="#c8161d"/><path d="M3.5 6.8l2 2 4-4" fill="none" stroke="#fff" stroke-width="1.6"/></svg>CHF 50.00, goods transport trailer</li>
  </ul>
</section>
<a class="btn abs" style="left:144px;top:2554px;width:143px;height:43px">Book A Trip</a>
<a class="btn dark abs" style="left:298px;top:2554px;width:144px;height:43px">Learn More</a>
<div class="abs" role="img" aria-label="Two friends laughing beside the coach" style="left:600px;top:2210px;width:455px;height:443px;background:linear-gradient(135deg,#8fa47a,#4a4e52 55%,#1f1f22)"></div>

<section class="gallery abs">
  <h2 class="section-title" style="margin-top:50px">OUR <span class="underline">GALLERY</span></h2>
  <div class="gph" role="img" aria-label="White minibus" style="left:0;top:135px;width:189px;height:260px;background:linear-gradient(135deg,#e4e6e8,#c9ccd0);opacity:.55"></div>
  <div class="gph" role="img" aria-label="Silver minibus on a mountain road" style="left:204px;top:135px;width:221px;height:260px;background:linear-gradient(180deg,#9fb1c2,#8a8f92 55%,#6b6a66)"></div>
  <div class="gph" role="img" aria-label="Silver minibus parked by trees" style="left:440px;top:123px;width:320px;height:283px;background:linear-gradient(180deg,#7c8a6a,#9ea3a6 55%,#7b7b78)"></div>
  <div class="gph" role="img" aria-label="Minibus seating interior" style="left:774px;top:135px;width:221px;height:260px;background:linear-gradient(180deg,#d8d8d6,#6b625a)"></div>
  <div class="gph" role="img" aria-label="White van on the road" style="left:1010px;top:135px;width:190px;height:260px;background:linear-gradient(135deg,#e8ebee,#c5cacf);opacity:.55"></div>
  <div class="arrow" style="left:550px;top:430px;background:var(--white);border:1px solid #ddd"><svg width="18" height="10" viewBox="0 0 18 10"><path d="M17 5H2M6 1L2 5l4 4" fill="none" stroke="#333" stroke-width="1.5"/></svg></div>
  <div class="arrow" style="left:606px;top:430px;background:var(--red)"><svg width="18" height="10" viewBox="0 0 18 10"><path d="M1 5h15M12 1l4 4-4 4" fill="none" stroke="#fff" stroke-width="1.5"/></svg></div>
</section>

<footer class="footer abs">
  <div class="brand" style="margin-top:62px"><span>Falk Brenz</span></div>
  <nav style="margin-top:26px"><a>Start</a><a>About Us</a><a>Day Trips</a><a>Holiday Trips</a><a>Group Tours</a><a>Airport Transfer</a><a>Minibus Rental</a><a>The Driver Making</a><a>Terms &amp; Conditions</a></nav>
  <div style="width:912px;height:1px;background:#6d6d6d;margin:20px auto 0"></div>
  <p style="font-size:12px;margin-top:18px">COPYRIGHT© 2025 FALK BRENZ &nbsp;|&nbsp; ALL RIGHTS RESERVED</p>
  <div style="margin-top:22px">
    <span class="social"></span>
    <span class="social" style="background:var(--red)"></span>
    <span class="social"><svg width="13" height="10" viewBox="0 0 13 10"><rect x=".5" y=".5" width="12" height="9" rx="1" fill="#333"/><path d="M1 1l5.5 4.5L12 1" fill="none" stroke="#fff" stroke-width="1"/></svg></span>
  </div>
</footer>

</body>
</html>
```